TALMORK

The business want a professional looking business card. We have a scetch we will add but want the extra upgrade, and would like more suggestions for variations of our business cards.

```html
<!DOCTYPE html>
<html lang="en">
<head>
<meta charset="utf-8">
<title>TALMORK business card</title>
<link rel="stylesheet" href="https://fonts.googleapis.com/css2?family=Playfair+Display:ital,wght@0,700;1,700&family=Montserrat:wght@400;600&display=swap">
<style>
  :root {
    --page-bg: #2a2a2a;
    --card-bg: #141414;
    --card-edge: #0a0a0a;
    --gold: #c99a32;
    --gold-light: #e2b954;
    --ink-light: #f2f2f2;
  }
  * { box-sizing: border-box; margin: 0; padding: 0; }
  html, body {
    width: 1200px; height: 900px; overflow: hidden;
    background: var(--page-bg);
  }
  .canvas {
    width: 1200px; height: 900px;
    display: flex; flex-direction: column; align-items: center; justify-content: center;
    gap: 60px;
  }
  .card {
    width: 560px; height: 320px;
    background: var(--card-bg);
    border-radius: 22px;
    box-shadow: 0 0 0 1px var(--card-edge), 0 18px 40px rgba(0,0,0,.45);
    position: relative;
    overflow: hidden;
  }

  /* Front: brand face */
  .card-front {
    display: flex; flex-direction: column; align-items: center; justify-content: center;
  }
  .brand-name-large {
    font-family: "Playfair Display", serif;
    font-weight: 700;
    font-size: 76px;
    letter-spacing: 4px;
    color: var(--gold);
    line-height: 1;
  }
  .brand-since-large {
    margin-top: 18px;
    font-family: "Montserrat", sans-serif;
    font-weight: 600;
    font-size: 15px;
    letter-spacing: 12px;
    color: var(--gold);
    padding-left: 12px;
  }

  /* Back: contact face */
  .card-back {
    display: flex; align-items: center;
    padding: 0 36px 0 38px;
  }
  .brand-block {
    width: 200px;
    display: flex; flex-direction: column; align-items: center;
  }
  .brand-dot {
    width: 38px; height: 38px; border-radius: 50%;
    background: var(--gold);
    margin-bottom: 12px;
  }
  .brand-name-small {
    font-family: "Playfair Display", serif;
    font-weight: 700;
    font-size: 34px;
    letter-spacing: 1px;
    color: var(--gold);
    line-height: 1;
  }
  .brand-since-small {
    margin-top: 8px;
    font-family: "Montserrat", sans-serif;
    font-weight: 600;
    font-size: 8px;
    letter-spacing: 5px;
    color: var(--gold);
  }
  .divider {
    width: 1px; height: 150px;
    background: var(--gold);
    margin: 0 30px 0 22px;
  }
  .person-block { flex: 1; }
  .person-name {
    font-family: "Playfair Display", serif;
    font-style: italic;
    font-weight: 700;
    font-size: 25px;
    color: var(--gold-light);
    line-height: 1.15;
  }
  .person-title {
    margin-top: 6px;
    font-family: "Montserrat", sans-serif;
    font-size: 13px;
    color: var(--ink-light);
  }
  .contact-list {
    list-style: none;
    margin-top: 18px;
    display: flex; flex-direction: column; gap: 8px;
  }
  .contact-item {
    display: flex; align-items: center; gap: 9px;
    font-family: "Montserrat", sans-serif;
    font-size: 12.5px;
    color: var(--ink-light);
  }
  .contact-icon { width: 12px; height: 12px; flex: none; }
</style>
</head>
<body>
<main class="canvas">

  <section class="card card-front" aria-label="Business card front">
    <div class="brand-name-large">TALMORK</div>
    <div class="brand-since-large">SINCE 2026</div>
  </section>

  <section class="card card-back" aria-label="Business card back">
    <div class="brand-block">
      <div class="brand-dot"></div>
      <div class="brand-name-small">TALMORK</div>
      <div class="brand-since-small">SINCE 2026</div>
    </div>
    <div class="divider"></div>
    <div class="person-block">
      <div class="person-name">Henrik Aslaksen Brenna</div>
      <div class="person-title">CEO &amp; Founder</div>
      <ul class="contact-list">
        <li class="contact-item">
          <svg class="contact-icon" viewBox="0 0 12 12" aria-hidden="true">
            <path d="M2.5 1h2l1 2.5-1.3 1a6 6 0 0 0 3.3 3.3l1-1.3 2.5 1v2a1 1 0 0 1-1 1A9.5 9.5 0 0 1 1.5 2a1 1 0 0 1 1-1z" fill="#f2f2f2"/>
          </svg>
          004790417726
        </li>
        <li class="contact-item">
          <svg class="contact-icon" viewBox="0 0 12 12" aria-hidden="true">
            <rect x="0.5" y="2" width="11" height="8" rx="1" fill="#f2f2f2"/>
            <path d="M1 2.6 6 6.5l5-3.9" fill="none" stroke="#141414" stroke-width="1"/>
          </svg>
          talmork.llc@mailbox.com
        </li>
        <li class="contact-item">
          <svg class="contact-icon" viewBox="0 0 12 12" aria-hidden="true">
            <circle cx="6" cy="6" r="5.2" fill="none" stroke="#f2f2f2" stroke-width="1.1"/>
            <ellipse cx="6" cy="6" rx="2.2" ry="5.2" fill="none" stroke="#f2f2f2" stroke-width="1"/>
            <path d="M1 6h10" stroke="#f2f2f2" stroke-width="1"/>
          </svg>
          www.talmork.llc
        </li>
      </ul>
    </div>
  </section>

</main>
</body>
</html>
```